****Business Card Design for Quarrystone Development. Design based around attached logo/company name

I’m looking for business card design for my company Quarrystone Development Group,LLC. Design should be professional, sharp and minimal. Outside of the attached logos, greyscale colors for remainder of cards. My thoughts are two-sided card with attached logo on one side and my info on the other but open to one-sided as well with right design.
Target Market(s)
Real estate professionals including banks, private investors, property owners, developers, commercial tenants like Brewlantern, Grovika or Tanquist’s.
Industry/Entity Type
Commercial real estate development and investments.
Contact Information for Business Card
Name, title, email, phone #’s, web address and physical address
Font styles to use
Other font styles liked:
- Helvetica, Garamond, etc
Colors
Designer to choose only greyscale colors for use in the design.
Requirements
Must have
- Attached logo first or second options.
Nice to have
- Two sided card with logo on one side. Attached Logo/company name can be laid out any way that flows as long as it’s legible.name
Should not have
- No loud colors. ***Please do not include logo, I have removed the company design with a logo image.

```html
<!DOCTYPE html>
<html lang="en">
<head>
<meta charset="utf-8">
<title>Quarrystone Development Group, LLC — Business Card</title>
<link rel="stylesheet" href="https://fonts.googleapis.com/css2?family=Cinzel:wght@400;700&family=Arimo:wght@400&display=swap">
<style>
  :root {
    --slate: #5b6577;
    --slate-light: #8a93a3;
    --paper: #ffffff;
    --ink-soft: #6e7788;
    --backdrop: #e4e3e0;
    --on-slate: #f4f5f7;
  }
  * { box-sizing: border-box; margin: 0; padding: 0; }
  html, body {
    width: 1200px; height: 900px; overflow: hidden;
    background: var(--backdrop);
  }
  .canvas {
    position: relative; width: 1200px; height: 900px;
  }
  .card {
    position: absolute; left: 320px; width: 560px; height: 320px;
    box-shadow: 0 6px 18px rgba(0,0,0,0.18);
    overflow: hidden;
  }
  /* Front side */
  .card-front { top: 90px; background: var(--slate); }
  .front-wordmark {
    position: absolute; left: 0; right: 0; top: 118px;
    text-align: center; color: var(--on-slate);
    font-family: "Cinzel", serif; font-weight: 400;
  }
  .front-wordmark .name { font-size: 40px; letter-spacing: 2px; line-height: 1; }
  .front-wordmark .rule {
    width: 330px; height: 1px; margin: 8px auto 7px; background: var(--on-slate); opacity: .7;
  }
  .front-wordmark .sub { font-size: 13px; letter-spacing: 3px; }

  /* Back side */
  .card-back { top: 490px; background: var(--paper); }
  .back-wordmark {
    position: absolute; left: 44px; top: 44px;
    color: var(--slate); font-family: "Cinzel", serif; font-weight: 400;
  }
  .back-wordmark .name { font-size: 30px; letter-spacing: 1.5px; line-height: 1; }
  .back-wordmark .rule { width: 250px; height: 1px; background: var(--slate-light); margin: 6px 0 5px; }
  .back-wordmark .sub { font-size: 10px; letter-spacing: 2.2px; }
  .brand-circle {
    position: absolute; right: 62px; top: 40px;
  }
  .person {
    position: absolute; left: 44px; top: 170px; color: var(--slate);
  }
  .person .full-name {
    font-family: "Cinzel", serif; font-weight: 700; font-size: 21px; letter-spacing: 1px;
  }
  .person .title {
    font-family: "Arimo", sans-serif; font-size: 14px; color: var(--ink-soft); margin-top: 2px;
  }
  .contact-list {
    position: absolute; left: 44px; top: 222px; list-style: none;
    font-family: "Arimo", sans-serif; font-size: 13px; color: var(--ink-soft);
  }
  .contact-list li { display: flex; align-items: center; gap: 8px; height: 19px; }
  .contact-list svg { width: 11px; height: 11px; fill: none; stroke: var(--slate); stroke-width: 1.6; }
  .address-band {
    position: absolute; left: 0; right: 0; bottom: 0; height: 34px;
    background: var(--slate); color: var(--on-slate);
    font-family: "Arimo", sans-serif; font-size: 13px;
    display: flex; align-items: center; justify-content: flex-end; padding-right: 30px;
  }
</style>
</head>
<body>
<main class="canvas">
  <section class="card card-front" aria-label="Card front">
    <div class="front-wordmark">
      <div class="name">QUARRYSTONE</div>
      <div class="rule"></div>
      <div class="sub">DEVELOPMENT GROUP, LLC</div>
    </div>
  </section>

  <section class="card card-back" aria-label="Card back">
    <div class="back-wordmark">
      <div class="name">QUARRYSTONE</div>
      <div class="rule"></div>
      <div class="sub">DEVELOPMENT GROUP, LLC</div>
    </div>

    <svg class="brand-circle" width="130" height="130" viewBox="0 0 130 130" aria-hidden="true">
      <circle cx="65" cy="65" r="58" fill="none" stroke="var(--slate)" stroke-width="6"/>
    </svg>

    <div class="person">
      <div class="full-name">DANIEL WHITCOMB</div>
      <div class="title">Director</div>
    </div>

    <ul class="contact-list">
      <li>
        <svg viewBox="0 0 12 12"><path d="M3 1.5 L4.6 3.6 L3.6 4.8 Q4.8 7.4 7.2 8.4 L8.4 7.4 L10.5 9 L9.4 10.6 Q4.6 10.2 1.4 2.6 Z"/></svg>
        (541) 555-0186
      </li>
      <li>
        <svg viewBox="0 0 12 12"><rect x="1" y="2.5" width="10" height="7"/><path d="M1 2.5 L6 6.5 L11 2.5"/></svg>
        info@quarrystonegroup.com
      </li>
      <li>
        <svg viewBox="0 0 12 12"><circle cx="6" cy="6" r="5"/><path d="M1 6 H11 M6 1 Q3 6 6 11 Q9 6 6 1"/></svg>
        www.quarrystonegroup.com
      </li>
    </ul>

    <div class="address-band">1187 Larkspur Lane Corvallis, OR 97330</div>
  </section>
</main>
</body>
</html>
```